Lock Company Van

The Meridian Lock Company needs a design for the side and back of our service vans.
Updates

Target Market(s)

B2B, Retail Stores, Individual Customers

Industry/Entity Type

Locksmith

Requirements
Must have
• "Protect yourself with THE MERIDIAN" as a tagline.

```html
<!DOCTYPE html>
<html lang="en">
<head>
<meta charset="utf-8">
<title>The Meridian Lock Company – Van Livery</title>
<link rel="stylesheet" href="https://fonts.googleapis.com/css2?family=Poppins:wght@600;700&display=swap">
<style>
  :root {
    --paint-white: #ffffff;
    --brand-red: #e3141b;
    --ink-grey: #4a4d52;
    --accent-red-soft: rgba(227, 20, 27, 0.85);
  }
  html, body {
    margin: 0;
    padding: 0;
    overflow: hidden;
  }
  body {
    width: 1200px;
    height: 900px;
    background: var(--paint-white);
  }
  .livery {
    position: relative;
    width: 1200px;
    height: 900px;
    overflow: hidden;
    background: var(--paint-white);
    font-family: "Poppins", Arial, sans-serif;
  }
  .brand-block {
    position: absolute;
    top: 120px;
    left: 0;
    width: 1200px;
    display: flex;
    justify-content: center;
    align-items: center;
    gap: 22px;
    z-index: 2;
  }
  .brand-mark {
    width: 38px;
    height: 38px;
    border-radius: 50%;
    background: var(--brand-red);
  }
  .brand-name {
    margin: 0;
    color: var(--brand-red);
    font-weight: 700;
    font-size: 50px;
    letter-spacing: 0.5px;
    text-transform: uppercase;
  }
  .tagline {
    position: absolute;
    top: 300px;
    left: 0;
    width: 1200px;
    margin: 0;
    text-align: center;
    font-weight: 700;
    line-height: 1.1;
    z-index: 2;
  }
  .tagline-lead {
    display: block;
    color: var(--ink-grey);
    font-size: 76px;
  }
  .tagline-name {
    display: block;
    color: var(--brand-red);
    font-size: 66px;
  }
  .corner-ring {
    position: absolute;
    left: -110px;
    top: 560px;
    overflow: visible;
    z-index: 1;
  }
</style>
</head>
<body>
  <main class="livery">
    <header class="brand-block">
      <span class="brand-mark" aria-hidden="true"></span>
      <h1 class="brand-name">The Meridian Lock Company</h1>
    </header>

    <p class="tagline">
      <span class="tagline-lead">Protect yourself with</span>
      <span class="tagline-name">THE MERIDIAN</span>
    </p>

    <svg class="corner-ring" width="440" height="440" viewBox="0 0 440 440" aria-hidden="true">
      <circle cx="220" cy="220" r="180" fill="none" stroke="var(--accent-red-soft)" stroke-width="50"/>
    </svg>
  </main>
</body>
</html>
```